ORLA - Óptica Médica - web design and concept

Website concept - Create and develop our website design and structure. ORLA is an optical store chain, and we are looking to establish our web and digital concept. In attachment there are several pictures about our stores and our logo.

The website structure should be user friendly. Colors should be light and the design as simple and minimalist as possible. There are different variations of the logothat can be used, check the file.

The website will include optical collections and sun collections as an online store. Also, a medical menu should be considered in order for clients to schedule optometry appointments. There should also be a menu for client assistance where the clients can read about glass maintenance in our workshop.
Updates

Low design quality

Number of Pages Required

5+ page

Font styles to use
Serif
Sans Serif

Requirements
Must have
• Must be user-friendly and minimalist.
• Please USE PICTURES FROM THE BRANDS we sell: MERUN, BOSKA, PNW, KOLE, BAMPE
Nice to have
• Nice to inspire: ZEK glasses (see website https://ch.shopzek.com/en/)
• Nice to inspire: https://merun-eyewear.com/
• Nice to ispire: https://www.pnwglobe.com/en/
Should not have
• Hysteric colors and shapes

```html
<!DOCTYPE html>
<html lang="en">
<head>
<meta charset="utf-8">
<title>ORLA – Sun Collection</title>
<link rel="stylesheet" href="https://fonts.googleapis.com/css2?family=Raleway:wght@200;300;400;600&display=swap">
<style>
:root{
  --accent:#f0b04c;
  --ink:#222;
  --muted:#777;
  --line:#d9d9d9;
  --tile:#f4f5f7;
  --footer:#000;
  --white:#fff;
}
*{box-sizing:border-box;margin:0;padding:0}
html,body{width:1200px;height:2951px;overflow:hidden;background:var(--white)}
body{font-family:"Raleway",Arial,sans-serif;color:var(--ink);position:relative}
.abs{position:absolute}
/* hero */
.hero{left:0;top:0;width:1200px;height:566px;background:linear-gradient(90deg,#d8d4cf 0%,#e6e3df 25%,#dfe3e8 55%,#cfd5de 100%)}
.hero-photo{left:0;top:0;width:620px;height:566px;background:radial-gradient(ellipse at 45% 45%,#c9a88a 0%,#d6c3b1 35%,rgba(220,220,222,0) 75%)}
.social{left:161px;top:16px;display:flex;gap:10px}
.social span{width:11px;height:11px;border-radius:50%;background:var(--ink)}
.brand{left:540px;top:12px;width:120px;text-align:center}
.brand .mark{display:block;width:22px;height:22px;margin:0 auto 6px;border:1px solid var(--ink)}
.brand .name{font-size:22px;letter-spacing:4px;font-weight:400}
.topbar{top:14px;font-size:10px;display:flex;align-items:center;gap:6px}
.nav{left:466px;top:103px;display:flex;gap:18px;align-items:center;font-size:11px}
.nav .active{color:var(--accent)}
.nav .cta{background:var(--accent);padding:5px 10px;color:var(--ink)}
.hero-title{left:734px;top:235px;font-size:92px;font-weight:200;letter-spacing:2px}
/* breadcrumb */
.crumb{left:161px;top:617px;font-size:11px;color:var(--muted)}
.crumb b{font-weight:400;color:var(--accent)}
/* sidebar */
.divider{left:328px;top:684px;width:2px;height:1277px;background:#bbb}
.side h3{font-size:15px;font-weight:400;left:161px}
.side ul{list-style:none;left:200px;font-size:11px;color:var(--muted);line-height:21px}
.side ul.box li{position:relative}
.side ul.box li::before{content:"";position:absolute;left:-38px;top:7px;width:7px;height:7px;border:1px solid var(--line)}
.side ul.sel li:first-child{color:var(--accent)}
.side ul.sel li:first-child::before{content:"";position:absolute;left:-18px;top:7px;border-left:5px solid var(--accent);border-top:4px solid transparent;border-bottom:4px solid transparent}
.swatches{left:161px;top:1518px;display:grid;grid-template-columns:repeat(4,33px);gap:4px}
.swatches span{height:33px}
.more{left:233px;top:1610px;border-top:8px solid var(--ink);border-left:5px solid transparent;border-right:5px solid transparent}
/* collection */
.coll-title{left:382px;top:675px;font-size:26px;font-weight:300}
.view{top:680px;width:22px;height:22px;display:grid;grid-template-columns:repeat(3,1fr);gap:2px}
.view span{background:var(--accent)}
.view.list span{background:var(--ink)}
.filterbar{top:751px;font-size:10px;display:flex;gap:10px;align-items:center}
.select{border:1px solid var(--accent);height:20px;display:flex;align-items:center;font-size:10px}
.select em{font-style:normal;padding:0 8px}
.select i{width:18px;height:20px;background:var(--accent);position:relative}
.select i::after{content:"";position:absolute;left:5px;top:8px;border-top:5px solid var(--white);border-left:4px solid transparent;border-right:4px solid transparent}
.product{width:200px;text-align:center}
.product .shot{width:170px;height:80px;margin:0 auto;border-radius:36px 36px 46px 46px}
.product p{margin-top:22px;font-size:15px;font-weight:300;color:#444}
.pager{left:826px;top:1938px;font-size:16px;display:flex;gap:5px;align-items:center}
.pager .on{color:var(--accent)}
/* newsletter */
.news-title{left:0;width:1200px;top:2053px;text-align:center;font-size:24px;font-weight:300}
.news-rule{left:536px;top:2090px;width:128px;height:4px;border-top:1px solid var(--accent);border-bottom:1px solid var(--accent)}
.news-form{left:303px;top:2128px;width:594px;height:69px;border:1px solid #bbb;display:flex}
.news-form span{flex:1;padding:26px 30px;font-size:11px;color:var(--muted)}
.news-form button{width:92px;border:0;background:var(--accent);display:flex;align-items:center;justify-content:center}
/* partner brands */
.partner{top:2278px;width:148px;height:116px;background:var(--tile);display:flex;align-items:center;justify-content:center;font-size:17px;font-weight:600;letter-spacing:1px;text-align:center}
.arrow{top:2314px}
/* features */
.feature{top:2473px;width:285px;height:88px;border:2px solid #e6e6e6;display:flex;align-items:center;justify-content:center;gap:12px}
.feature strong{display:block;font-weight:300;font-size:16px;color:#555}
.feature small{font-size:10px;color:#555}
/* footer */
.footer{left:0;top:2628px;width:1200px;height:323px;background:var(--footer);color:var(--white)}
.footer h4{position:absolute;top:92px;font-size:12px;font-weight:600;color:var(--accent);letter-spacing:.5px}
.footer ul{position:absolute;top:120px;list-style:none;font-size:10px;line-height:17px}
.footer ul li::before{content:"•";margin-right:8px}
.f-brand{left:161px;top:60px;position:absolute;width:160px}
.f-brand .name{color:var(--accent);font-size:20px;letter-spacing:3px}
.f-brand p{font-size:10px;line-height:13px;margin-top:8px}
.f-brand .read{font-size:10px;margin-top:8px}
.f-social{display:flex;gap:9px;margin-top:10px}
.f-social span{width:10px;height:10px;border-radius:50%;background:var(--accent)}
.contact{position:absolute;left:860px;top:120px;font-size:10px;line-height:17px}
.contact div{display:flex;gap:8px;align-items:flex-start;margin-bottom:6px}
.f-rule{position:absolute;left:161px;top:224px;width:880px;height:1px;background:#555}
.f-copy{position:absolute;left:161px;top:240px;font-size:11px}
.f-legal{position:absolute;left:820px;top:235px;font-size:11px}
</style>
</head>
<body>

<header>
  <div class="abs hero" role="img" aria-label="Smiling woman in a straw hat lifting her sunglasses, beside a travel suitcase handle"></div>
  <div class="abs hero-photo"></div>
  <div class="abs social"><span></span><span></span><span></span><span></span><span></span></div>
  <div class="abs brand"><span class="mark"></span><div class="name">ORLA</div></div>
  <div class="abs topbar" style="left:822px">
    <svg width="10" height="11" viewBox="0 0 10 11"><rect x="1" y="5" width="8" height="6" fill="#222"/><path d="M3 5V3a2 2 0 0 1 4 0v2" stroke="#222" fill="none"/></svg>
    Your Cart ( 0 )
  </div>
  <div class="abs topbar" style="left:935px">
    <svg width="10" height="10" viewBox="0 0 10 10"><path d="M2 0l2 3-1 1q1 2 3 3l1-1 3 2-1 2Q3 9 0 2z" fill="#222"/></svg>
    +000-555-0142
  </div>
  <nav class="abs nav">
    <span>Home</span><span class="active">Sun</span><span>Optical</span><span>Store</span><span>Contact Us</span><span class="cta">Make an Appoiment</span>
  </nav>
  <h1 class="abs hero-title">SUN</h1>
</header>

<main>
  <div class="abs crumb">Home / <b>Sun</b></div>

  <aside class="side">
    <div class="abs divider"></div>
    <h3 class="abs" style="top:743px">Filter</h3>
    <ul class="abs sel" style="top:787px"><li>ALL</li><li>Men</li><li>Women</li><li>Kids</li></ul>
    <h3 class="abs" style="top:932px">Material</h3>
    <ul class="abs box" style="top:973px"><li>Acetate</li><li>Titanium</li><li>Wire</li></ul>
    <h3 class="abs" style="top:1101px">Size</h3>
    <ul class="abs box" style="top:1143px"><li>Small</li><li>Medium</li><li>Large</li></ul>
    <h3 class="abs" style="top:1276px">Foam</h3>
    <ul class="abs box" style="top:1320px"><li>Rectangular</li><li>Round</li><li>Round-Rectangular</li></ul>
    <h3 class="abs" style="top:1471px">Colours</h3>
    <div class="abs swatches">
      <span style="background:#e8212b"></span><span style="background:#a8a8a8"></span><span style="background:#12e58f"></span><span style="background:#2cf24a"></span>
      <span style="background:#ffc20e"></span><span style="background:#ee1f9c"></span><span style="background:#10e8f0"></span><span style="background:#000"></span>
    </div>
    <div class="abs more"></div>
  </aside>

  <section>
    <h2 class="abs coll-title">Full Collection</h2>
    <div class="abs view" style="left:978px"><span></span><span></span><span></span><span></span><span></span><span></span><span></span><span></span><span></span></div>
    <div class="abs view list" style="left:1023px;grid-template-columns:1fr 1fr"><span></span><span></span><span></span><span></span></div>

    <div class="abs filterbar" style="left:386px">Collection <div class="select"><em>Full</em><i></i></div></div>
    <div class="abs filterbar" style="left:652px">Show <div class="select"><em>12</em><i></i></div></div>
    <div class="abs filterbar" style="left:890px">Show <div class="select"><em>Recommended</em><i></i></div></div>

    <div class="abs product" style="left:364px;top:855px"><div class="shot" role="img" aria-label="Black sunglasses with grey lenses" style="background:linear-gradient(#2a2f36,#5b6670)"></div><p>Product Name</p></div>
    <div class="abs product" style="left:622px;top:855px"><div class="shot" role="img" aria-label="Cat-eye sunglasses with purple lenses" style="background:linear-gradient(#3a2a5c,#8a6fb0)"></div><p>Product Name</p></div>
    <div class="abs product" style="left:866px;top:855px"><div class="shot" role="img" aria-label="Sunglasses with rose gradient lenses" style="background:linear-gradient(#5a2a3a,#d4a3ae)"></div><p>Product Name</p></div>

    <div class="abs product" style="left:364px;top:1106px"><div class="shot" role="img" aria-label="Wood-frame square sunglasses" style="background:linear-gradient(#7a3f1c,#56503f)"></div><p>Product Name</p></div>
    <div class="abs product" style="left:622px;top:1106px"><div class="shot" role="img" aria-label="Aviator sunglasses with blue lenses" style="background:linear-gradient(#1e2b44,#8aa1c0)"></div><p>Product Name</p></div>
    <div class="abs product" style="left:866px;top:1106px"><div class="shot" role="img" aria-label="Black cat-eye sunglasses" style="background:linear-gradient(#1b1b1f,#9a98a5)"></div><p>Product Name</p></div>

    <div class="abs product" style="left:364px;top:1374px"><div class="shot" role="img" aria-label="Tortoiseshell sunglasses with brown lenses" style="background:linear-gradient(#5a2a10,#c0834e)"></div><p>Product Name</p></div>
    <div class="abs product" style="left:622px;top:1374px"><div class="shot" role="img" aria-label="Double-bridge aviator sunglasses" style="background:linear-gradient(#2c2a38,#b8b4c4)"></div><p>Product Name</p></div>
    <div class="abs product" style="left:866px;top:1374px"><div class="shot" role="img" aria-label="Brown sunglasses with gradient lenses" style="background:linear-gradient(#2b1c16,#bba69a)"></div><p>Product Name</p></div>

    <div class="abs product" style="left:364px;top:1664px"><div class="shot" role="img" aria-label="Round black sunglasses" style="background:linear-gradient(#151a20,#5e6c78)"></div><p>Product Name</p></div>
    <div class="abs product" style="left:622px;top:1664px"><div class="shot" role="img" aria-label="Shield sunglasses with dark blue lenses" style="background:linear-gradient(#0f1a2c,#6f86a6)"></div><p>Product Name</p></div>
    <div class="abs product" style="left:866px;top:1664px"><div class="shot" role="img" aria-label="Cat-eye sunglasses with violet lenses" style="background:linear-gradient(#2a1a4e,#8b70bb)"></div><p>Product Name</p></div>

    <div class="abs pager">
      <svg width="10" height="12" viewBox="0 0 10 12"><path d="M7 1L2 6l5 5" stroke="#222" stroke-width="2" fill="none"/></svg>
      <span class="on">1</span><span>2</span><span>3</span><span>4</span><span>5</span><span>6</span><span>7</span><span>8</span><span>9</span>
      <svg width="10" height="12" viewBox="0 0 10 12"><path d="M3 1l5 5-5 5" stroke="#f0b04c" stroke-width="2" fill="none"/></svg>
    </div>
  </section>

  <section>
    <h2 class="abs news-title">Subscribe For Our Newsletter</h2>
    <div class="abs news-rule"></div>
    <div class="abs news-form">
      <span>E-Mail Address</span>
      <button aria-label="Subscribe"><svg width="34" height="28" viewBox="0 0 34 28"><path d="M2 2l30 12L2 26l5-12z M7 14h25" stroke="#222" stroke-width="2" fill="none" stroke-linejoin="round"/></svg></button>
    </div>
  </section>

  <section>
    <svg class="abs arrow" style="left:78px" width="24" height="44" viewBox="0 0 24 44"><path d="M20 2L4 22l16 20" stroke="#222" stroke-width="2" fill="none"/></svg>
    <div class="abs partner" style="left:161px">Solvane</div>
    <div class="abs partner" style="left:344px">Haldor</div>
    <div class="abs partner" style="left:527px">Mira Lune</div>
    <div class="abs partner" style="left:709px">Cevrin</div>
    <div class="abs partner" style="left:891px">Tovu Eyewear</div>
    <svg class="abs arrow" style="left:1100px" width="24" height="44" viewBox="0 0 24 44"><path d="M4 2l16 20L4 42" stroke="#f0b04c" stroke-width="2" fill="none"/></svg>
  </section>

  <section>
    <div class="abs feature" style="left:165px">
      <svg width="26" height="26" viewBox="0 0 26 26"><circle cx="13" cy="11" r="9" stroke="#f0b04c" stroke-width="2" fill="none"/><path d="M13 20v5" stroke="#f0b04c" stroke-width="2"/></svg>
      <div><strong>Free Shipping</strong><small>Lorem Ipsum is dummy text.</small></div>
    </div>
    <div class="abs feature" style="left:460px">
      <svg width="26" height="26" viewBox="0 0 26 26"><circle cx="13" cy="8" r="5" stroke="#f0b04c" stroke-width="2" fill="none"/><path d="M3 25a10 10 0 0 1 20 0" stroke="#f0b04c" stroke-width="2" fill="none"/></svg>
      <div><strong>Premium Support</strong><small>24/7 Customer service</small></div>
    </div>
    <div class="abs feature" style="left:753px">
      <svg width="32" height="24" viewBox="0 0 32 24"><path d="M1 3h19v14H1z M20 8h6l5 5v4H20z" stroke="#f0b04c" stroke-width="2" fill="none"/><circle cx="7" cy="19" r="3" fill="#fff" stroke="#f0b04c" stroke-width="2"/><circle cx="25" cy="19" r="3" fill="#fff" stroke="#f0b04c" stroke-width="2"/></svg>
      <div><strong>Payment Method</strong><small>Cash On Delivery</small></div>
    </div>
  </section>
</main>

<footer class="abs footer">
  <div class="f-brand">
    <div class="name">ORLA</div>
    <p>Lorem Ipsum is simply dummy text of the printing and typesetting industry.</p>
    <div class="read">READ MORE....</div>
    <div class="f-social"><span></span><span></span><span></span><span></span><span></span></div>
  </div>
  <h4 style="left:423px">QUICK LINK</h4>
  <ul style="left:423px"><li>Women</li><li>Men</li><li>Youth</li><li>Collections</li><li>Contact Us</li></ul>
  <h4 style="left:635px">ACCOUNT</h4>
  <ul style="left:635px"><li>My Account</li><li>My Whislist</li><li>Checkout</li><li>Create Account</li><li>Register</li></ul>
  <h4 style="left:860px">QUICK CONTACT</h4>
  <div class="contact">
    <div><svg width="10" height="10" viewBox="0 0 10 10"><path d="M2 0l2 3-1 1q1 2 3 3l1-1 3 2-1 2Q3 9 0 2z" fill="#f0b04c"/></svg>+000-555-0198</div>
    <div><svg width="10" height="8" viewBox="0 0 10 8"><rect width="10" height="8" fill="#f0b04c"/><path d="M0 0l5 4 5-4" stroke="#000" fill="none"/></svg>info@orlaeyecare.com</div>
    <div><svg width="8" height="11" viewBox="0 0 8 11"><path d="M4 11L1 6a3.5 3.5 0 1 1 6 0z" fill="#f0b04c"/></svg><span>14 Alder Ave.<br>Brookfield Township, NJ 07000</span></div>
  </div>
  <div class="f-rule"></div>
  <div class="f-copy">CopyRight ©2018 Orla Eyecare. All Right Reserve</div>
  <div class="f-legal">Privacy Policy - Terms &amp; Conditions</div>
</footer>

</body>
</html>
```